Detail Shop Business card design

i need a business card design for my new detailing company called 'Brisk's Polish Works'. i want an all black and white design . simple, direct and to the point. i want the designer to choose a fitting font to match the logothe front should have logo, address, phone and email and the back side should have a slogan and text indicating that we offer services on anything including cars, trucks, motorcycles and RVs. slogan will read "we take pride in your ride"
maybe also very small on the back side the IG icon with Brisks_Polish_Works

phone 208.417.6352
address 3847 E Larkin Ave
Spokane WA 99214
email: BrisksPolish@mailvexo.com

Target Market(s)

all ages , auto enthusiasts

Industry/Entity Type

Automotive

Contact Information for Business Card

the front should have logo, address, phone and email and the back side should have a slogan and text indicating that we offer services on anything including cars, trucks, motorcycles and RVs. slogan will read "we take pride in your ride"

phone 208.417.6352
address 3847 E Larkin Ave
Spokane WA 99214

Colors
000000
ffffff

Requirements
Must have
• bold font and very simple design with good spacing
Nice to have
• anything creative from the designer indicating we service any types of vehicles
Should not have
• any colors ,

```html
<!DOCTYPE html>
<html lang="en">
<head>
<meta charset="utf-8">
<title>Brisk's Polish Works – Business Card</title>
<link rel="stylesheet" href="https://fonts.googleapis.com/css2?family=Lato:ital,wght@0,400;0,700;1,400&display=swap">
<style>
  :root {
    --page-bg: #e9e7e5;
    --card-black: #050505;
    --ink-white: #ffffff;
    --ink-soft: #f2f2f2;
    --rule: #4a4a4a;
    --badge-light: #ffffff;
    --badge-shade: #dcdcdc;
    --badge-ink: #0a0a0a;
  }
  * { box-sizing: border-box; margin: 0; padding: 0; }
  html, body {
    width: 1200px;
    height: 900px;
    overflow: hidden;
    background: var(--page-bg);
    font-family: "Lato", Arial, sans-serif;
  }
  .business-card {
    position: absolute;
    left: 160px;
    top: 178px;
    width: 880px;
    height: 543px;
    background: var(--card-black);
    border-radius: 18px;
    color: var(--ink-white);
  }
  .contact-line {
    position: absolute;
    left: 46px;
    display: flex;
    align-items: center;
    gap: 6px;
    font-size: 24px;
    line-height: 1;
    color: var(--ink-soft);
  }
  .contact-line svg { flex: none; }
  .phone { top: 62px; }
  .email { top: 95px; }
  .address {
    position: absolute;
    left: 46px;
    top: 144px;
    font-size: 24px;
    line-height: 32px;
    color: var(--ink-soft);
  }
  .social { top: 238px; }
  .social-dot {
    width: 26px;
    height: 26px;
    border-radius: 50%;
    background: var(--ink-white);
    margin-right: 4px;
  }
  .services {
    position: absolute;
    left: 46px;
    top: 320px;
    font-size: 23px;
    font-style: italic;
    line-height: 33px;
    color: var(--ink-soft);
  }
  .services .indent { padding-left: 6px; }
  .divider {
    position: absolute;
    left: 46px;
    top: 437px;
    width: 341px;
    height: 1px;
    background: var(--rule);
  }
  .slogan {
    position: absolute;
    left: 46px;
    top: 462px;
    font-size: 24px;
    letter-spacing: 0.3px;
    color: var(--ink-white);
  }
  .brand-badge {
    position: absolute;
    left: 387px;
    top: 46px;
    width: 450px;
    height: 450px;
    border-radius: 50%;
    background: radial-gradient(circle at 40% 35%, var(--badge-light) 0%, var(--ink-soft) 55%, var(--badge-shade) 100%);
    display: flex;
    align-items: center;
    justify-content: center;
    text-align: center;
  }
  .brand-name {
    font-weight: 700;
    font-size: 46px;
    line-height: 54px;
    color: var(--badge-ink);
  }
</style>
</head>
<body>
  <section class="business-card">
    <p class="contact-line phone">
      <svg width="20" height="18" viewBox="0 0 20 18" aria-hidden="true">
        <path d="M1 6 Q10 -1 19 6 L16 8 L14 5 H6 L4 8 Z" fill="#fff"/>
        <rect x="4" y="9" width="12" height="8" rx="1.5" fill="#fff"/>
      </svg>
      208.417.6352
    </p>
    <p class="contact-line email">
      <svg width="20" height="16" viewBox="0 0 20 16" aria-hidden="true">
        <rect x="1" y="2" width="18" height="12" fill="#fff"/>
        <path d="M1 2 L10 9 L19 2" fill="none" stroke="#050505" stroke-width="1.6"/>
      </svg>
      BrisksPolish@mailvexo.com
    </p>
    <p class="address">3847 E Larkin Ave<br>Spokane WA 99214</p>
    <p class="contact-line social"><span class="social-dot"></span>Brisks_Polish_Works</p>
    <p class="services">We offer services on<br>anything including&nbsp; cars<br><span class="indent">trucks motorcycles and RVs</span></p>
    <div class="divider"></div>
    <p class="slogan">WE TAKE PRIDE IN YOUR RID</p>
    <div class="brand-badge">
      <p class="brand-name">Brisk's<br>Polish Works</p>
    </div>
  </section>
</body>
</html>
```